"Harbor Builders" is a residential building company and needs a new business card design and may re

We would like a redesign based on the existing logo, and would like to see a new font as well. We are bespoke home builders who build sustainable energy efficient homes.

Industry/Entity Type

Construction

Contact Information for Business Card

Business card size 40mm x 90mm

Colors

Designer to choose colors to be used in the design.

```html
<!DOCTYPE html>
<html lang="en">
<head>
<meta charset="utf-8">
<title>Harbor Builders – Business Card</title>
<link rel="stylesheet" href="https://fonts.googleapis.com/css2?family=Roboto:wght@400;500&family=Roboto+Condensed:wght@500;700&display=swap">
<style>
  :root {
    --backdrop: #5b5853;
    --card-light: #f4f4f3;
    --card-dark: #1c1d1f;
    --ink: #1a1a1a;
    --ink-soft: #4a4a4a;
    --lime: #b5d334;
  }
  * { box-sizing: border-box; margin: 0; padding: 0; }
  html, body {
    width: 1200px; height: 960px; overflow: hidden;
    background: var(--backdrop);
  }
  .canvas { position: relative; width: 1200px; height: 960px; }

  .card {
    position: absolute;
    box-shadow: 0 3px 8px rgba(0,0,0,0.35);
  }
  .card-front {
    left: 302px; top: 129px; width: 600px; height: 342px;
    background: var(--card-light);
    color: var(--ink-soft);
    font-family: "Roboto", Arial, sans-serif;
  }
  .card-back {
    left: 300px; top: 488px; width: 598px; height: 343px;
    background: var(--card-dark);
  }

  /* brand name standing in for the mark */
  .brand {
    position: absolute;
    display: flex; align-items: center; gap: 12px;
    font-family: "Roboto", Arial, sans-serif;
    font-weight: 500;
  }
  .brand-front { right: 26px; top: 62px; color: var(--ink); font-size: 26px; }
  .brand-back  { left: 0; right: 0; top: 126px; justify-content: center; color: var(--lime); font-size: 46px; }
  .brand-square { display: block; background: var(--lime); }
  .brand-front .brand-square { width: 22px; height: 22px; }
  .brand-back .brand-square { width: 38px; height: 38px; }

  .holder-name {
    position: absolute; left: 31px; top: 124px;
    font-family: "Roboto Condensed", "Arial Narrow", sans-serif;
    font-weight: 500; font-size: 22px; color: var(--ink);
    letter-spacing: 0.2px;
  }
  .details {
    position: absolute; left: 31px; top: 159px;
    font-size: 14px; line-height: 18px;
  }
  .company { font-weight: 500; }
  .registration { margin-top: 3px; margin-left: 1px; }
  .contact-list { list-style: none; margin-top: 6px; margin-left: 1px; }
  .contact-list li { display: flex; align-items: center; gap: 8px; height: 19.5px; }
  .contact-icon { width: 13px; height: 13px; flex: none; }

  .web-back {
    position: absolute; left: 0; right: 0; top: 296px;
    text-align: center;
    font-family: "Roboto", Arial, sans-serif;
    font-size: 14px; letter-spacing: 2.3px;
    color: var(--lime);
  }
</style>
</head>
<body>
<main class="canvas">

  <section class="card card-front" aria-label="Business card front">
    <div class="brand brand-front">
      <span class="brand-square"></span>
      <span class="brand-name">Harbor Builders</span>
    </div>

    <h1 class="holder-name">DANIEL MORROW</h1>

    <div class="details">
      <p class="company">Harbor Builders Pty Ltd</p>
      <p>PO Box 2140 Eastgate</p>
      <p>LPO Ridgeview WA 6099</p>
      <div class="registration">
        <p>Registration 48210</p>
        <p>ABN: 42 305 718 664</p>
      </div>
      <ul class="contact-list">
        <li>
          <svg class="contact-icon" viewBox="0 0 13 13" aria-hidden="true">
            <rect x="3" y="0.5" width="7" height="12" rx="1.2" fill="none" stroke="#1a1a1a" stroke-width="1.4"/>
            <rect x="4.4" y="2" width="4.2" height="7.5" fill="#1a1a1a"/>
          </svg>
          <span>0400 123 456</span>
        </li>
        <li>
          <svg class="contact-icon" viewBox="0 0 13 13" aria-hidden="true">
            <rect x="0.5" y="3" width="12" height="8" fill="#1a1a1a"/>
            <path d="M0.5 3 L6.5 7.5 L12.5 3" fill="none" stroke="#f4f4f3" stroke-width="1.1"/>
          </svg>
          <span>daniel@harborbuilders.com.au</span>
        </li>
        <li>
          <svg class="contact-icon" viewBox="0 0 13 13" aria-hidden="true">
            <circle cx="6.5" cy="6.5" r="6" fill="#1a1a1a"/>
            <path d="M3 4 Q5 3 6 5 Q5 7 4 8 M8 9 Q9 7 10.5 8" fill="none" stroke="#f4f4f3" stroke-width="1.2"/>
          </svg>
          <span>www.harborbuilders.com.au</span>
        </li>
      </ul>
    </div>
  </section>

  <section class="card card-back" aria-label="Business card back">
    <div class="brand brand-back">
      <span class="brand-square"></span>
      <span class="brand-name">Harbor Builders</span>
    </div>
    <p class="web-back">www.harborbuilders.com.au</p>
  </section>

</main>
</body>
</html>
```